Mira Ellsworth ADHD coach needs a flyer

I need a flyer to be sent by email. the copy is attached. It can be changed/reduced to fit the flyer. I would like to keep my website colors. My website is www.miraellsworth.net - Thank you!

```html
<!DOCTYPE html>
<html lang="en">
<head>
<meta charset="utf-8">
<title>Mira Ellsworth – Academic Success Coaching</title>
<link href="https://fonts.googleapis.com/css2?family=Montserrat:wght@700;800&family=Source+Sans+3:ital,wght@0,400;0,600;0,700;1,600;1,700&display=swap" rel="stylesheet">
<style>
  :root{
    --backdrop:#e6e8e9;
    --paper:#ffffff;
    --teal:#7d9ca7;
    --teal-head:#7f9ea9;
    --teal-photo-a:#7d9ca5;
    --teal-photo-b:#9bb4bb;
    --ink:#231f20;
    --white:#ffffff;
  }
  *{box-sizing:border-box;margin:0;padding:0}
  html,body{width:898px;height:1200px;overflow:hidden;background:var(--backdrop)}
  body{font-family:"Source Sans 3",sans-serif;color:var(--ink)}
  .flyer{position:absolute;left:24px;top:0;width:849px;height:1200px;background:var(--paper);overflow:hidden}
  .abs{position:absolute}

  .hero{left:0;top:44px;width:849px;height:271px;background:linear-gradient(100deg,var(--teal-photo-a),var(--teal-photo-b) 45%,var(--teal-photo-a) 80%,var(--teal-photo-b))}
  .hero-title{left:40px;top:88px;width:748px;text-align:center;font-family:"Montserrat",sans-serif;font-weight:800;font-size:35px;line-height:40px;color:var(--white);white-space:nowrap}
  .hero-sub{left:40px;top:224px;width:748px;text-align:center;font-style:italic;font-weight:700;font-size:21px;line-height:23px;color:var(--white);white-space:nowrap}
  .hero-chevrons{left:757px;top:52px}

  .intro{left:81px;top:332px;width:690px;font-size:13.3px;line-height:15.7px;font-weight:400}
  .intro p+p{margin-top:15.7px}

  .panel{background:var(--teal);color:var(--white)}
  .panel-how{left:79px;top:528px;width:320px;height:587px}
  .panel-how .photo{position:absolute;left:130px;top:11px;width:180px;height:218px;background:radial-gradient(ellipse at 50% 45%,#c9b7b4 0,#aab6ba 45%,rgba(125,156,167,0) 75%)}
  .panel-title{font-family:"Montserrat",sans-serif;font-weight:700;font-size:22px;line-height:24px}
  .panel-sub{font-weight:600;font-size:16.5px;line-height:21px;margin-top:4px;white-space:nowrap}
  .how-head{position:absolute;left:20px;top:18px}
  .how-head .panel-sub{font-size:17.5px}
  .how-chevrons{position:absolute;left:24px;top:104px}
  .how-body{position:absolute;left:19px;top:240px;width:290px;font-size:13.3px;line-height:15px;font-weight:400}
  .how-lead{font-weight:700;margin-top:14px;margin-bottom:6px}
  .how-list{list-style:none}
  .how-list li{position:relative;padding-left:16px;margin-bottom:6px}
  .how-list li::before{content:"";position:absolute;left:1px;top:3px;border-left:7px solid var(--white);border-top:4px solid transparent;border-bottom:4px solid transparent}

  .panel-potential{left:420px;top:528px;width:349px;height:291px;padding:13px 0 0 24px}
  .pot-title{display:flex;align-items:center;gap:10px}
  .square-list{list-style:none;margin-top:4px;font-size:13.3px;line-height:19px;font-weight:400}
  .square-list li{position:relative;padding-left:12px}
  .square-list li::before{content:"";position:absolute;left:1px;top:8px;width:4px;height:4px;background:var(--white)}
  .pot-second{font-weight:600;font-size:17.5px;line-height:22px;margin-top:14px}

  .voices{left:420px;top:832px;width:347px;font-size:13.2px;line-height:15px}
  .voice-head{display:flex;align-items:center;gap:8px;color:var(--teal-head);font-family:"Montserrat",sans-serif;font-weight:700;font-size:13px;line-height:16px;margin:0 0 8px}
  .voice-head::after{content:"";flex:1;height:1px;background:var(--ink);opacity:.6}
  .voices blockquote{margin-bottom:14px}
  .voices blockquote+.voice-head{margin-top:-2px}
  .voices b{font-weight:700}

  .footer{left:0;top:1130px;width:849px;height:70px;background:var(--teal);color:var(--white)}
  .next{position:absolute;left:72px;top:14px;font-family:"Montserrat",sans-serif;font-weight:700;font-size:20px;line-height:21px}
  .next-arrow{position:absolute;left:152px;top:16px}
  .next-text{position:absolute;left:204px;top:16px;font-weight:700;font-size:17px;line-height:18px;white-space:nowrap}
  .site{position:absolute;left:626px;top:23px;width:188px;height:25px;border:1.5px solid var(--white);text-align:center;font-weight:700;font-size:15px;line-height:22px}
</style>
</head>
<body>
<main class="flyer">
  <section class="abs hero" role="img" aria-label="Photo of smiling college students sitting together outdoors, tinted teal"></section>
  <h1 class="abs hero-title">Helping Your Child with ADHD or<br>Other Learning Challenges Thrive<br>in College and Beyond</h1>
  <p class="abs hero-sub">Academic success coaching that leads to lifelong transformation<br>for students with ADHD and similar challenges that may have<br>impeded their ability to thrive.</p>
  <svg class="abs hero-chevrons" width="34" height="165" viewBox="0 0 34 165" fill="none" stroke="#fff" stroke-width="2.2">
    <path d="M2 2l15 10 15-10M2 22l15 10 15-10M2 42l15 10 15-10M2 62l15 10 15-10M2 90l15 10 15-10M2 110l15 10 15-10M2 130l15 10 15-10M2 150l15 10 15-10"/>
  </svg>

  <div class="abs intro">
    <p>Sending your child off to college can feel scary, especially if that college is hundreds of miles away. You worry about how they’ll do on their own—whether they’ll make friends, earn good grades, and be happy—especially without you there to support them daily. You know your child is bright, and you want them to have a great future, but you’re concerned they will struggle without the right support and resources.</p>
    <p>You don’t need to feel helpless as you send your child off to this next stage of their lives. Mira is dedicated to making that transition easier for everyone. Mira Ellsworth has years of experience helping students thrive despite their challenges. She sees your child’s potential and helps them see it, too. She provides a safety net as they adjust to a new environment at college. Her services are comprehensive and adaptable, based on the requirements of each individual: helping with course selection and scheduling, time management, study strategies, focus, making new friends, and adapting to change. Through it all, Mira guides students through fundamental work on mindset to ensure that changes stick.</p>
  </div>

  <section class="abs panel panel-how">
    <div class="photo" role="img" aria-label="Portrait of Mira Ellsworth in a pale pink blazer, arms crossed"></div>
    <div class="how-head">
      <h2 class="panel-title">Empowering<br>Focus:</h2>
      <p class="panel-sub">How Mira Helps</p>
    </div>
    <svg class="how-chevrons" width="30" height="112" viewBox="0 0 30 112" fill="none" stroke="#fff" stroke-width="2">
      <path d="M1 2l14 9 14-9M1 18l14 9 14-9M1 34l14 9 14-9M1 50l14 9 14-9M1 66l14 9 14-9M1 82l14 9 14-9M1 98l14 9 14-9"/>
    </svg>
    <div class="how-body">
      <p>Mira has taken students from failing to a 3.0 GPA, and from a C student to the Dean’s List, in just one semester. It doesn’t take years to provide lasting results; all it takes is the right guide.</p>
      <p class="how-lead">Uniquely positioned to help your child, Mira:</p>
      <ul class="how-list">
        <li>Tailors support so that your child improves focus and maximizes their potential in college and beyond.</li>
        <li>Understands your child’s unique needs - she sees the gifts that others often miss.</li>
        <li>Knows the academic landscape intimately, including the challenges faced by students with ADHD and other conditions.</li>
        <li>Helps with the logistics of scheduling in a way that most advisors can’t, enrolling students in the courses that best suit their learning style.</li>
        <li>Nurtures the brilliance in your bright child.</li>
        <li>Provides a balance between encouraging students and challenging them.</li>
      </ul>
    </div>
  </section>

  <section class="abs panel panel-potential">
    <div class="pot-title">
      <h2 class="panel-title">Realizing Potential:</h2>
      <svg width="22" height="24" viewBox="0 0 22 24" fill="none" stroke="#fff" stroke-width="1.6"><path d="M2 2l8 10-8 10M11 2l8 10-8 10"/></svg>
    </div>
    <p class="panel-sub">The Transformation You’ll See in Your Child</p>
    <ul class="square-list">
      <li>A mindset of self-belief and increased confidence.</li>
      <li>Higher grades and the drive to graduate.</li>
      <li>Social integration and making friends.</li>
      <li>Happiness and fulfilment.</li>
      <li>A deep sense of personal achievement and pride.</li>
    </ul>
    <p class="pot-second">You Will Have:</p>
    <ul class="square-list">
      <li>Less stress, knowing that your child is in good hands.</li>
      <li>Fewer sleepless nights worrying about your child.</li>
      <li>Confidence that they are receiving the right support.</li>
      <li>Joy and pride at seeing them do well.</li>
    </ul>
  </section>

  <section class="abs voices">
    <h3 class="voice-head">What Parents Say</h3>
    <blockquote>“Mira was the glue that kept our daughter in college… as our daughter’s Academic Coach, [she] gave our daughter the ability to finish strong by empowering her with the skills needed to be successful.” -<b>Renee</b></blockquote>
    <blockquote>“Mira has always told my daughter not that she can succeed, but that she will succeed.”- <b>Laura</b></blockquote>
    <h3 class="voice-head">What Students Say</h3>
    <blockquote>“Last semester I completed all 16 hours and I had the highest GPA I’ve ever had!” -<b>Former student</b></blockquote>
    <blockquote>“Under her instruction, my grades began to improve. I ended up making the Dean’s List during my time at Ridgemont, and I was also inducted into Phi Kappa Delta. I am currently in my first year of law school at Fairhaven University, a top tier school.”- <b>Former student</b></blockquote>
  </section>

  <footer class="abs footer">
    <p class="next">NEXT<br>STEPS</p>
    <svg class="next-arrow" width="30" height="36" viewBox="0 0 30 36" fill="none" stroke="#fff" stroke-width="1.8"><path d="M2 2l11 16L2 34M15 2l11 16-11 16"/></svg>
    <p class="next-text">To learn more and discuss your child’s individual needs,<br>call 334·555·0142 or email coach@miraellsworth.net</p>
    <p class="site">www.miraellsworth.net</p>
  </footer>
</main>
</body>
</html>
```